Business Card Design Project

Beam Clinic Hub

Dr Lomen Priscu M.D, F.R.C.S
Vascular and Vein Surgery

47-15 Quillford Avenue, Suite 318
Astoria
NY 11103

212-555-0183
718-555-0146
www.mendorapro.us back of the card for scheduled appointments up to 5 appointment dates

Target Market(s)

Male and Female patients from 25 onwards with spider veins or varicose veins

Industry/Entity Type

Business

Font styles to use
Serif

Colors
86cae6
85abd2
0456a4

Requirements
Must have
• Modern Sophisticated design using light blue and grey text
Should not have
• hearts or flowers

```html
<!DOCTYPE html>
<html lang="en">
<head>
<meta charset="utf-8">
<title>Beam Clinic Hub – Business Card</title>
<link rel="stylesheet" href="https://fonts.googleapis.com/css2?family=Lora:wght@400;500&display=swap">
<style>
  :root {
    --backdrop: #e9e6e1;
    --card-light: #ffffff;
    --card-shade: #e3e4e6;
    --accent: #86cae6;
    --accent-mid: #85abd2;
    --accent-deep: #0456a4;
    --ink: #55595e;
    --ink-soft: #8a8e93;
  }
  * { box-sizing: border-box; margin: 0; padding: 0; }
  html, body {
    width: 1057px; height: 1200px; overflow: hidden;
    background: var(--backdrop);
    font-family: "Lora", Georgia, serif;
  }
  .canvas { position: relative; width: 1057px; height: 1200px; }
  .card {
    position: absolute; left: 368px; width: 320px; height: 560px;
    background: radial-gradient(ellipse at 45% 40%, var(--card-light) 0%, var(--card-shade) 100%);
    box-shadow: 0 6px 18px rgba(0,0,0,.18);
    overflow: hidden;
  }
  .card--front { top: 30px; }
  .card--back { top: 610px; }

  .accent-band {
    position: absolute; top: 0; bottom: 0; left: 258px; width: 22px;
    background: var(--accent);
  }
  .brand { color: var(--accent); font-weight: 400; line-height: 1.15; }
  .card--front .brand {
    position: absolute; top: 34px; right: 76px; text-align: right; font-size: 32px;
  }

  .person { position: absolute; top: 150px; right: 72px; text-align: right; }
  .person__name { color: var(--accent-mid); font-size: 14px; letter-spacing: 1.2px; text-transform: uppercase; }
  .person__credentials { color: var(--accent-mid); font-size: 10px; letter-spacing: 1px; margin-top: 2px; }
  .person__role { color: var(--ink-soft); font-size: 8px; letter-spacing: 1px; text-transform: uppercase; margin-top: 4px; }

  .details { position: absolute; right: 62px; left: 14px; }
  .details--address { top: 222px; }
  .details--contact { top: 300px; }
  .detail {
    display: flex; justify-content: flex-end; align-items: flex-end;
    font-size: 10.5px; color: var(--ink); height: 20px; white-space: nowrap;
  }
  .detail__rule {
    width: 22px; border-bottom: 1px solid var(--accent); margin-left: 4px; margin-bottom: -3px;
  }

  .card--back .brand {
    position: absolute; top: 60px; left: 44px; font-size: 38px;
  }
  .appointments { position: absolute; top: 200px; left: 34px; right: 34px; }
  .appointments__title {
    color: var(--accent-mid); font-size: 11px; letter-spacing: 1.5px;
    text-transform: uppercase; margin-bottom: 14px;
  }
  .slot {
    display: flex; align-items: flex-end; gap: 8px;
    font-size: 10px; color: var(--ink-soft); height: 36px;
  }
  .slot__line { flex: 1; border-bottom: 1px solid var(--accent); margin-bottom: 3px; }
  .slot__line--short { flex: 0 0 64px; }

  .web-line {
    position: absolute; left: 26px; right: 40px; bottom: 44px;
    display: flex; align-items: center; gap: 12px;
    font-size: 10px; color: var(--ink);
    border-bottom: 1px solid var(--ink-soft); padding-bottom: 8px;
  }
  .web-line__mark { width: 12px; height: 12px; border-radius: 50%; background: var(--accent); }
  .web-line__rule {
    position: absolute; left: 0; right: 0; top: -10px; border-top: 1px solid var(--accent);
  }
</style>
</head>
<body>
<main class="canvas">
  <section class="card card--front" aria-label="Card front">
    <div class="accent-band"></div>
    <h1 class="brand">Beam Clinic<br>Hub</h1>
    <div class="person">
      <p class="person__name">Dr Lomen Priscu</p>
      <p class="person__credentials">M.D, F.R.C.S</p>
      <p class="person__role">Vascular and Vein Surgery</p>
    </div>
    <div class="details details--address">
      <p class="detail">47-15 Quillford Avenue, Suite 318<span class="detail__rule"></span></p>
      <p class="detail">Astoria, NY 11103<span class="detail__rule"></span></p>
    </div>
    <div class="details details--contact">
      <p class="detail">212-555-0183<span class="detail__rule"></span></p>
      <p class="detail">718-555-0146<span class="detail__rule"></span></p>
      <p class="detail">www.mendorapro.us<span class="detail__rule"></span></p>
    </div>
  </section>

  <section class="card card--back" aria-label="Card back">
    <h2 class="brand">Beam Clinic<br>Hub</h2>
    <div class="appointments">
      <p class="appointments__title">Your Appointments</p>
      <div class="slot">Date<span class="slot__line"></span>Time<span class="slot__line slot__line--short"></span></div>
      <div class="slot">Date<span class="slot__line"></span>Time<span class="slot__line slot__line--short"></span></div>
      <div class="slot">Date<span class="slot__line"></span>Time<span class="slot__line slot__line--short"></span></div>
      <div class="slot">Date<span class="slot__line"></span>Time<span class="slot__line slot__line--short"></span></div>
      <div class="slot">Date<span class="slot__line"></span>Time<span class="slot__line slot__line--short"></span></div>
    </div>
    <div class="web-line">
      <span class="web-line__rule"></span>
      <span class="web-line__mark"></span>
      <span>www.mendorapro.us</span>
    </div>
  </section>
</main>
</body>
</html>
```